Brightwell Aero Services Logo

I need a website and logo for the parent company Brightwell Aero Services, which encompasses general aviation aircraft repair, small aircrat rental and flight school. The company is based in Lawrenceville, Georgia at the Tolleson county airport. A saying that can be incorporated somehere could be, "Quality flying is safe flying", "Safety in mind is no accident" ,. I need a website and logo.

The company started as a repair shop performing repairs and inspections on Harlan, Vantor, Delkin and Ralstead general aviation aircraft, all models of single engine piston, multi engine piston, and single engine turboprop with an emphasis on Harlan Solvane and AeroTurn turbo prop aircraft. We have se=ince entered the aircraft rental and flight instruction market using the Delkin 240 ang Harlan Ranger aircraft.

Number of Pages; I don't know. Maybe 5 ? A home page for Brightwell Aero Services, page for maintenance and repairs and a couple for the rental and school. The maintenance shop is busy, always has been. I need to get the rental and school advertised and busy.

I have a logo for the maintenance shop shirts, not for the school. I do not have the file. I paid a business locally to do that and print on the shirts. They have the file.

Target Market(s)

In our flight school rental fleet department, we are looking for persons wishing to obtain their private pilot license and continuing on into their commercial and instrument ratings. In the aircraft maintenance department, we are looking for new customers who want a better and more quality relationship with their aircraft maintenance provider who will give more detail and quality in the repairs with an emphasis on safety and fewer problems between scheduled maintenance cycles on their aircraft. Brightwell's owner, Dale Hutchins, has been performing aircraft maintenance in the Atlanta area for 27 years. He has built a steady customer base through those years.

```html
<!DOCTYPE html>
<html lang="en">
<head>
<meta charset="utf-8">
<title>Brightwell Aero Services</title>
<link rel="stylesheet" href="https://fonts.googleapis.com/css2?family=Jost:wght@400;500;600&display=swap">
<style>
:root{
  --navy:#152a44;
  --red:#e8393a;
  --white:#ffffff;
  --ink:#1d2b3e;
  --muted:#6b7380;
  --line:#d7dbe0;
}
*{box-sizing:border-box;margin:0;padding:0}
html,body{width:1200px;height:3271px;overflow:hidden}
body{position:relative;font-family:'Jost',sans-serif;color:var(--ink);background:var(--white)}
.abs{position:absolute}
a{color:inherit;text-decoration:none}

/* header */
.site-header{left:0;top:0;width:1200px;height:69px;background:var(--white);z-index:3}
.brand-disc{left:66px;top:-110px;width:252px;height:252px;border-radius:50%;background:var(--white);z-index:4}
.brand{left:108px;top:22px;z-index:5;display:flex;align-items:center;gap:10px}
.brand-dot{width:26px;height:26px;border-radius:50%;background:var(--red)}
.brand-name{font-weight:600;font-size:17px;line-height:1.05;color:var(--navy)}
.brand-name small{display:block;font-size:9px;letter-spacing:3px;font-weight:600}
.main-nav{left:590px;top:0;height:69px;display:flex;gap:34px;align-items:center;font-size:14px;z-index:5}
.main-nav a{position:relative}
.main-nav a.active{color:var(--red)}
.main-nav a.active::after{content:"";position:absolute;left:0;right:0;bottom:-24px;height:2px;background:var(--red)}
.btn{display:flex;align-items:center;justify-content:center;background:var(--red);color:var(--white);border-radius:20px;font-weight:500;font-size:14px}
.quote-btn{left:949px;top:17px;width:138px;height:37px;z-index:5}

/* hero */
.hero{left:0;top:69px;width:1200px;height:642px;background:linear-gradient(120deg,#3b3a35 0%,#5c5a52 35%,#8a8a86 60%,#4a4944 100%)}
.hero-shade{left:0;top:69px;width:1200px;height:642px;background:linear-gradient(90deg,rgba(0,0,0,.35),rgba(0,0,0,0) 60%)}
.hero-title{left:110px;top:326px;font-size:56px;font-weight:500;color:var(--white);line-height:1.1}
.hero-text{left:110px;top:397px;width:470px;font-size:15px;line-height:22px;color:var(--white)}
.hero-btn{left:110px;top:453px;width:139px;height:35px}
.dots{left:565px;top:644px;display:flex;gap:7px}
.dots span{width:12px;height:12px;border-radius:50%;border:2px solid var(--white)}
.dots span.on{background:var(--red);border-color:var(--red)}

.section-title{left:0;width:1200px;text-align:center;font-size:45px;font-weight:500;color:var(--navy)}

/* services */
.service{width:362px;height:362px;border-radius:50%;background:var(--navy);color:var(--white);text-align:center;padding:42px 58px 0}
.service.featured{background:var(--red);z-index:2}
.service .icon{height:76px;display:flex;align-items:flex-end;justify-content:center}
.service h3{font-size:22px;font-weight:500;margin:12px 0 20px}
.service p{font-size:14px;line-height:21.5px;height:86px}
.service .go{width:40px;height:40px;border-radius:50%;background:var(--red);margin:22px auto 0;display:flex;align-items:center;justify-content:center}
.service.featured .go{background:var(--white)}

/* about */
.about{left:0;top:1328px;width:1200px;height:602px;background:var(--navy)}
.about-photo{left:0;top:1328px;width:640px;height:602px;background:linear-gradient(90deg,#5a5a57 0%,#6e6d69 45%,rgba(21,42,68,0.6) 80%,var(--navy) 100%)}
.about-title{left:616px;top:1410px;font-size:45px;font-weight:500;color:var(--white)}
.about-copy{left:616px;top:1484px;width:474px;color:var(--white);font-size:14.5px;line-height:21.5px;text-align:justify}
.about-copy p+p{margin-top:21px}
.about-btn{left:616px;top:1793px;width:138px;height:37px;gap:5px}

/* clients */
.client{top:2102px;width:183px;height:89px;background:var(--white);box-shadow:0 4px 14px rgba(0,0,0,.07);display:flex;align-items:center;justify-content:center;gap:8px;font-size:26px;font-weight:500;color:var(--navy)}
.client i{width:14px;height:14px;background:var(--red);display:block}
.arrow{top:2138px}

/* contact */
.info{width:220px;text-align:center}
.info .ring{width:54px;height:54px;border:2px solid var(--red);border-radius:50%;margin:0 auto;display:flex;align-items:center;justify-content:center}
.info h4{font-size:17px;font-weight:500;margin-top:14px;color:var(--ink)}
.info p{font-size:13.5px;color:var(--muted);line-height:21px;margin-top:3px}
.field{border:1px solid var(--line);border-radius:3px;padding:0 15px;font-size:13px;color:var(--ink);display:flex;align-items:center}
.field.area{align-items:flex-start;padding-top:14px}
.submit-btn{left:531px;top:2757px;width:138px;height:36px}

/* footer */
.site-footer{left:0;top:2897px;width:1200px;height:374px;background:var(--navy)}
.on-dark{color:var(--white)}
.foot-brand{left:112px;top:3010px;display:flex;align-items:center;gap:10px}
.foot-brand .brand-name{color:var(--white)}
.socials{left:156px;top:3080px;display:flex;gap:4px}
.socials span{width:30px;height:30px;border-radius:50%;background:var(--white);display:flex;align-items:center;justify-content:center}
.socials span::after{content:"";width:8px;height:8px;border-radius:50%;background:var(--navy)}
.foot-col h5{font-size:20px;font-weight:500;margin-bottom:18px;color:var(--white)}
.foot-col li{list-style:none;font-size:14px;line-height:21.5px;color:var(--white)}
.foot-contact li{display:flex;gap:14px;align-items:flex-start;margin-bottom:0}
.foot-contact svg{flex:none;margin-top:4px;width:16px}
.copyright{left:0;top:3216px;width:1200px;text-align:center;font-size:14px;color:var(--white)}
</style>
</head>
<body>

<header class="abs site-header"></header>
<div class="abs brand-disc"></div>
<a class="abs brand" href="#"><span class="brand-dot"></span><span class="brand-name">Brightwell Aero<small>SERVICES</small></span></a>
<nav class="abs main-nav">
  <a class="active" href="#">Home</a><a href="#">About us</a><a href="#">Services</a><a href="#">Contact</a>
</nav>
<a class="abs btn quote-btn" href="#">Get A Quote</a>

<section>
  <div class="abs hero" role="img" aria-label="Hangar interior with small aircraft under maintenance"></div>
  <div class="abs hero-shade"></div>
  <h1 class="abs hero-title">Brightwell Aero</h1>
  <p class="abs hero-text">Lorem ipsum dolor sit amet, consectetur adipiscing elit, sed do eiusmod tempor incididunt ut labore et dolore magna aliqua.</p>
  <a class="abs btn hero-btn" href="#">Get Started</a>
  <div class="abs dots"><span></span><span class="on"></span><span></span><span></span></div>
</section>

<section>
  <h2 class="abs section-title" style="top:772px">Our Services</h2>

  <article class="abs service" style="left:111px;top:863px">
    <div class="icon"><svg width="70" height="56" viewBox="0 0 70 56" fill="none" stroke="#fff" stroke-width="2.5"><path d="M4 52V22L35 4l31 18v30"/><path d="M14 52V28h42v24"/><path d="M14 36h42M14 44h42"/><path d="M30 44v-6h10v6"/></svg></div>
    <h3>Aircraft Repair</h3>
    <p>Lorem ipsum dolor sit amet, consec tetur adipiscing elit, sed do eiusmod tempor incididunt ut labore et dolore magna aliqua.</p>
    <div class="go"><svg width="12" height="12" viewBox="0 0 12 12" fill="none" stroke="#fff" stroke-width="2"><path d="M4 2l4 4-4 4"/></svg></div>
  </article>

  <article class="abs service featured" style="left:419px;top:863px">
    <div class="icon"><svg width="76" height="76" viewBox="0 0 76 76" fill="none" stroke="#fff" stroke-width="2.5"><path d="M30 4v50M20 20h20M12 32l18-6 18 6M24 50h12"/><circle cx="52" cy="54" r="16"/><path d="M48 46v8l4 4 4-4v-8"/></svg></div>
    <h3>Small Aircraft Rental</h3>
    <p>Lorem ipsum dolor sit amet, consectetur adipiscing elit, sed do eiusmod tempor incididunt ut labore et dolore magna aliqua.</p>
    <div class="go"><svg width="12" height="12" viewBox="0 0 12 12" fill="none" stroke="#e8393a" stroke-width="2"><path d="M4 2l4 4-4 4"/></svg></div>
  </article>

  <article class="abs service" style="left:727px;top:863px">
    <div class="icon"><svg width="72" height="72" viewBox="0 0 72 72" fill="none" stroke="#fff" stroke-width="2.5"><circle cx="36" cy="36" r="26"/><path d="M36 2v8M36 62v8M2 36h8M62 36h8M12 12l6 6M54 54l6 6M60 12l-6 6M12 60l6-6"/><path d="M16 38h40M36 26v20M28 48h16"/></svg></div>
    <h3>Flight School</h3>
    <p>Lorem ipsum dolor sit amet, consec tetur adipiscing elit, sed do eiusmod tempor incididunt ut labore et dolore magna aliqua.</p>
    <div class="go"><svg width="12" height="12" viewBox="0 0 12 12" fill="none" stroke="#fff" stroke-width="2"><path d="M4 2l4 4-4 4"/></svg></div>
  </article>
</section>

<section>
  <div class="abs about"></div>
  <div class="abs about-photo" role="img" aria-label="Technician working on a white aircraft inside the hangar"></div>
  <h2 class="abs about-title">About Us</h2>
  <div class="abs about-copy">
    <p>Lorem ipsum dolor sit amet, consectetur adipiscing elit, sed do eiusmod tempor incididunt ut labore et dolore magna aliqua. Ut enim ad minim veniam, quis nostrud exercitation ullamco laboris nisi ut aliquip ex ea commodo consequat. Duis aute irure dolor in reprehenderit in voluptate velit esse cillum dolore eu fugiat nulla pariatur.</p>
    <p>Excepteur sint occaecat cupidatat non proident, sunt in culpa qui officia deserunt mollit anim id est laborum. Lorem ipsum dolor sit amet, consectetur adipiscing elit, sed do eiusmod tempor incididunt ut labore et dolore magna aliqua. Ut enim ad minim veniam, quis nostrud exercitation ullamco laboris nisi ut aliquip ex ea commodo consequat. Duis aute irure dolor in reprehenderit in voluptate velit esse cillum dolore eu fugiat nulla pariatur.</p>
  </div>
  <a class="abs btn about-btn" href="#">Learn More <svg width="13" height="13" viewBox="0 0 14 14"><circle cx="7" cy="7" r="7" fill="#fff"/><path d="M6 4l3 3-3 3" stroke="#e8393a" stroke-width="2" fill="none"/></svg></a>
</section>

<section>
  <h2 class="abs section-title" style="top:2020px">Our Clients</h2>
  <svg class="abs arrow" style="left:100px" width="14" height="22" viewBox="0 0 14 22" fill="none" stroke="#1d2b3e" stroke-width="2"><path d="M10 5l-6 6 6 6"/></svg>
  <div class="abs client" style="left:211px"><i></i>Harlan</div>
  <div class="abs client" style="left:409px"><i></i>Vantor</div>
  <div class="abs client" style="left:608px"><i></i>Delkin</div>
  <div class="abs client" style="left:806px"><i></i>Ralstead</div>
  <svg class="abs arrow" style="left:1086px" width="14" height="22" viewBox="0 0 14 22" fill="none" stroke="#1d2b3e" stroke-width="2"><path d="M4 5l6 6-6 6"/></svg>
</section>

<section>
  <h2 class="abs section-title" style="top:2280px">Contact Us</h2>
  <div class="abs info" style="left:260px;top:2377px">
    <div class="ring"><svg width="12" height="16" viewBox="0 0 12 16"><path d="M6 0a6 6 0 0 0-6 6c0 4.5 6 10 6 10s6-5.5 6-10a6 6 0 0 0-6-6zm0 8.5a2.5 2.5 0 1 1 0-5 2.5 2.5 0 0 1 0 5z" fill="#1d2b3e"/></svg></div>
    <h4>Address :</h4>
    <p>Lorem ipsum dolor sit amet,<br>consectetur adipiscing</p>
  </div>
  <div class="abs info" style="left:490px;top:2377px">
    <div class="ring"><svg width="14" height="14" viewBox="0 0 14 14"><path d="M3 0l3 3-2 2c1 2 3 4 5 5l2-2 3 3-2 3C6 14 0 8 0 3z" fill="#1d2b3e"/></svg></div>
    <h4>Phone :</h4>
    <p>+1 888 888 8888</p>
  </div>
  <div class="abs info" style="left:718px;top:2377px">
    <div class="ring"><svg width="16" height="12" viewBox="0 0 16 12"><path d="M0 0h16v2L8 7 0 2zM0 4l8 5 8-5v8H0z" fill="#1d2b3e"/></svg></div>
    <h4>Email Address :</h4>
    <p>info@brightwellaero.com</p>
  </div>

  <div class="abs field" style="left:216px;top:2555px;width:235px;height:42px">Name</div>
  <div class="abs field" style="left:488px;top:2555px;width:235px;height:42px">Phone</div>
  <div class="abs field" style="left:758px;top:2555px;width:236px;height:42px">Email</div>
  <div class="abs field area" style="left:216px;top:2633px;width:779px;height:101px">Text here</div>
  <a class="abs btn submit-btn" href="#">Submit Now</a>
</section>

<footer class="abs site-footer"></footer>
<div class="abs foot-brand"><span class="brand-dot"></span><span class="brand-name">Brightwell Aero<small>SERVICES</small></span></div>
<div class="abs socials"><span aria-label="Social profile 1"></span><span aria-label="Social profile 2"></span><span aria-label="Social profile 3"></span><span aria-label="Social profile 4"></span></div>
<div class="abs foot-col on-dark" style="left:413px;top:2983px">
  <h5>Quick Links</h5>
  <ul><li>Home</li><li>About</li><li>Services</li><li>Portfolio</li><li>Clients</li><li>Contact</li></ul>
</div>
<div class="abs foot-col on-dark" style="left:621px;top:2983px">
  <h5>Information</h5>
  <ul><li>Privacy policy</li><li>Terms &amp; condition</li><li>Support</li><li>Faq</li><li>Team</li></ul>
</div>
<div class="abs foot-col foot-contact on-dark" style="left:832px;top:2983px;width:220px">
  <h5>Contact Us</h5>
  <ul>
    <li><svg height="14" viewBox="0 0 12 16"><path d="M6 0a6 6 0 0 0-6 6c0 4.5 6 10 6 10s6-5.5 6-10a6 6 0 0 0-6-6zm0 8.5a2.5 2.5 0 1 1 0-5 2.5 2.5 0 0 1 0 5z" fill="#fff"/></svg><span>123, Lorem ipsum dolor sit consectetur adipiscing elit sed do eius</span></li>
    <li><svg height="13" viewBox="0 0 14 14"><path d="M3 0l3 3-2 2c1 2 3 4 5 5l2-2 3 3-2 3C6 14 0 8 0 3z" fill="#fff"/></svg><span>+1 888 888 8888</span></li>
    <li><svg height="11" viewBox="0 0 16 12"><path d="M0 0h16v2L8 7 0 2zM0 4l8 5 8-5v8H0z" fill="#fff"/></svg><span>info@brightwellaero.com</span></li>
  </ul>
</div>
<p class="abs copyright">Copyright © 2023. All Rights Reserved</p>

</body>
</html>
```